Wordpress website design for a high-end painting business

We are currently rebranding and are looking to update our Wordpress theme. We have recently rebranded our logo on PixelHarbor, and would like our website to be equally as refined.
Our business is named “Fenwick Painters”. We are a high-end painting business that is known for being professional and having high standards. Our clean and professional image is important as it separates us from our competition. Our current website can be found at www.fenwickcoatings.co.nz . We designed the site ourselves so it is understandably rudimentary. We are generally happy with the. page layout of our existing site, but we like a professional remodel. Any ideas on improvement welcomed.
We would like the front page of the website to summarise all of the info throughout the whole website (I.e introduction, photos, testimonials, contact info etc.) as visitors typically scroll through the first page to see that we are reputable and get to our contact number/email contact at the bottom of the page. We would like this first page to give a clean well rounded image of our business. We would like the gallery to be a scroll through of large photos, as it is difficult to see paint details in smaller photos. A contact page with an enquiry section would also be good.
For the colour scheme, we would like something that fits a bold, masculine and high end theme (similar to our logo attached).
We would like the footer to include Velmora paint logos and the accredited painter logo we have included as these are important to our profession.
We have attached some photos of our work also. I will add more in the coming days. More can also be found on our website.
If you have questions or comments, please don’t hesitate to ask and I will get back as soon as possible.
We are open to your own interpretation or ideas for a better layout/site provided they fit the general brief of being a well rounded site for our profession.
Thanks,
Fenwick Painters.
Target Market(s)
High end clients
Industry/Entity Type
Painting (interior and exterior)
Coding
Coded - Design and coding required
Requirements
Must have
- Classy feel, separating us from typical painting companies. Well rounded homepage.
Nice to have
- Lots of examples of our work
Should not have
- Untidy paint motifs (eg, paint droplets, paint splashes)

```html
<!DOCTYPE html>
<html lang="en">
<head>
<meta charset="utf-8">
<title>Fenwick Painters</title>
<link href="https://fonts.googleapis.com/css2?family=Lora:wght@500;700&family=Roboto:wght@400;500;700&display=swap" rel="stylesheet">
<style>
:root{
  --brown:#7a5a36;
  --brown-deep:#6a4f30;
  --navy:#141a24;
  --light:#f1f2f4;
  --text:#6b6b6b;
  --white:#fff;
}
*{margin:0;padding:0;box-sizing:border-box}
html,body{width:1200px;height:3394px;overflow:hidden}
body{font-family:'Roboto',sans-serif;color:var(--navy);background:var(--white);position:relative}
.abs{position:absolute}
.serif{font-family:'Lora',serif}
.section-title{position:absolute;left:0;width:1200px;text-align:center;font-family:'Lora',serif;font-weight:700;font-size:36px;letter-spacing:.5px;color:var(--navy)}
.section-title .accent{color:var(--brown)}

/* header */
.site-header{position:absolute;top:0;left:0;width:1200px;height:103px;background:var(--white);z-index:5}
.top-bar{position:absolute;left:545px;top:0;width:540px;height:46px;background:var(--navy);border-radius:0 0 40px 40px;display:flex;align-items:center;gap:44px;padding-left:60px;color:#fff;font-size:14px}
.top-bar span{display:flex;align-items:center;gap:14px}
.top-icon{width:32px;height:32px;border-radius:50%;background:#fff;display:flex;align-items:center;justify-content:center}
.main-nav{position:absolute;top:66px;left:425px;display:flex;gap:0}
.main-nav a{font-family:'Lora',serif;font-weight:500;font-size:15px;color:var(--navy);text-decoration:none;margin-right:44px}
.main-nav a.active{color:var(--brown)}
.logo-badge{position:absolute;left:67px;top:-10px;width:180px;height:180px;border-radius:50%;background:#fff;z-index:6;display:flex;align-items:flex-end;justify-content:center;padding-bottom:38px}
.logo-name{font-family:'Lora',serif;font-weight:700;font-size:19px;color:var(--navy);text-align:center;line-height:1.1}

/* hero */
.hero{position:absolute;top:103px;left:0;width:1200px;height:600px;background:linear-gradient(180deg,#7d8ea0 0%,#8d8266 35%,#6d6148 65%,#3f5a2c 100%)}
.hero-text{position:absolute;top:205px;left:0;width:1200px;text-align:center;color:#fff}
.hero-text h1{font-family:'Lora',serif;font-weight:700;font-size:32px;letter-spacing:.5px}
.hero-text p{font-size:18px;font-weight:500;line-height:27px;margin-top:18px}
.btn-light{display:inline-block;margin-top:33px;background:#fff;color:var(--brown);font-weight:700;font-size:14px;padding:17px 28px;border-radius:30px}
.arrow-btn{position:absolute;width:38px;height:38px;border-radius:50%;background:#fff;display:flex;align-items:center;justify-content:center}
.hero-curve{position:absolute;left:0;top:0}
.hero-dot{position:absolute;left:560px;top:663px;width:80px;height:80px;border-radius:50%;background:#fff;border:3px solid var(--light);display:flex;align-items:center;justify-content:center;z-index:3}
.hero-dot i{width:44px;height:44px;border-radius:50%;background:var(--navy);display:block}

/* about */
.about{position:absolute;top:703px;left:0;width:1200px;height:524px;background:var(--light)}
.about-photo{position:absolute;left:145px;top:92px;width:350px;height:350px;border-radius:50%;background:radial-gradient(circle at 50% 40%,#c9cfd3,#8d9a84 60%,#4b6b3a)}
.about-text{position:absolute;left:644px;top:84px;width:446px}
.about-text h2{font-family:'Lora',serif;font-weight:700;font-size:34px}
.about-text h2 span{color:var(--brown)}
.about-text p{font-size:13.5px;line-height:26px;color:var(--text);margin-top:14px}
.about-text p+p{margin-top:12px}
.btn-brown{display:inline-block;margin-top:36px;background:var(--brown);color:#fff;font-weight:700;font-size:14px;padding:17px 24px;border-radius:30px}

/* services */
.services{position:absolute;top:1227px;left:0;width:1200px;height:573px}
.service{position:absolute;top:163px;width:232px;text-align:center}
.service-photo{width:232px;height:232px;border-radius:50%;background:linear-gradient(180deg,#9fb3c7,#8a7c66 55%,#527a3a);border-bottom:4px solid var(--navy);position:relative}
.service-icon{position:absolute;left:69px;top:179px;width:94px;height:94px;border-radius:50%;background:var(--navy);display:flex;align-items:center;justify-content:center}
.service h3{margin-top:67px;font-size:19px;font-weight:700;color:var(--brown);line-height:26px}
.outline-arrow{position:absolute;width:38px;height:38px;border-radius:50%;border:2px solid var(--navy);display:flex;align-items:center;justify-content:center}

/* testimonials */
.testimonials{position:absolute;top:1800px;left:0;width:1200px;height:497px;background:linear-gradient(180deg,#6f5535,#65492b)}
.testimonials .section-title{color:#fff;top:40px}
.t-card{position:absolute;top:130px;width:309px;height:273px;background:#fff;border-radius:8px;text-align:center;padding:20px 18px 0}
.avatar{width:76px;height:76px;border-radius:50%;background:linear-gradient(180deg,#c6b3a2,#7d6a5c);margin:0 auto}
.t-card p{font-size:12.5px;line-height:25px;color:var(--text);margin-top:14px;position:relative}
.t-card .name{font-family:'Lora',serif;font-weight:500;color:var(--brown);font-size:14px;position:absolute;left:0;width:100%;top:242px}
.quote-mark{position:absolute;font-family:'Lora',serif;font-size:80px;color:#e3e3e3;line-height:1}
.dots{position:absolute;top:2237px;left:574px;display:flex;gap:5px}
.dots i{width:9px;height:9px;border-radius:50%;background:#cfc6bb;display:block}
.dots i.on{background:#fff}

/* gallery */
.gallery{position:absolute;top:2297px;left:0;width:1200px;height:436px;overflow:hidden}
.g-photo{position:absolute;top:161px;width:232px;height:189px;border-radius:3px}

/* contact */
.contact{position:absolute;top:2733px;left:0;width:1200px;height:264px;background:var(--light)}
.c-item{position:absolute;top:130px;display:flex;align-items:center;gap:27px}
.c-icon{width:80px;height:80px;border-radius:50%;background:#fff;display:flex;align-items:center;justify-content:center}
.c-item h4{font-family:'Lora',serif;font-weight:700;font-size:14px;color:var(--navy)}
.c-item p{font-size:13.5px;line-height:21px;color:var(--text);margin-top:6px}

/* footer */
.footer{position:absolute;top:2997px;left:0;width:1200px;height:397px}
.footer-bg{position:absolute;left:0;top:0}
.footer-logo{position:absolute;left:111px;top:105px;width:120px;text-align:center;font-family:'Lora',serif;font-weight:700;font-size:21px;color:#fff;line-height:1.15}
.f-col{position:absolute;top:56px;color:#fff}
.f-col h5{font-family:'Lora',serif;font-weight:500;font-size:17px;margin-bottom:14px}
.f-col li{list-style:none;font-size:14px;line-height:25px;display:flex;align-items:flex-start;gap:20px}
.f-col li b{width:13px;height:13px;border-radius:50%;background:var(--brown);display:inline-block;margin-top:6px;flex:none}
.f-col li.gap{margin-bottom:8px}
.f-rule{position:absolute;left:111px;width:978px;height:1px;background:#39404c}
.badge{position:absolute;top:295px;height:40px;background:#fff;border-radius:2px}
.copyright{position:absolute;top:369px;left:0;width:1200px;text-align:center;color:#fff;font-family:'Lora',serif;font-size:12px}
</style>
</head>
<body>

<header class="site-header">
  <div class="logo-badge"><div class="logo-name">FENWICK<br><span style="font-size:11px;letter-spacing:2px">PAINTERS</span></div></div>
  <div class="top-bar">
    <span><i class="top-icon"><svg width="14" height="14" viewBox="0 0 24 24"><path fill="#141a24" d="M6.6 10.8a15 15 0 006.6 6.6l2.2-2.2c.3-.3.7-.4 1-.2 1.1.4 2.3.6 3.6.6.6 0 1 .4 1 1V20c0 .6-.4 1-1 1A17 17 0 013 4c0-.6.4-1 1-1h3.5c.6 0 1 .4 1 1 0 1.3.2 2.5.6 3.6.1.3 0 .7-.2 1z"/></svg></i>021 555 0148</span>
    <span><i class="top-icon"><svg width="14" height="12" viewBox="0 0 24 18"><path fill="#141a24" d="M0 0h24v2L12 9 0 2zM0 4l12 7 12-7v14H0z"/></svg></i>hello@fenwickpainters.co.nz</span>
  </div>
  <nav class="main-nav">
    <a class="active">HOME</a><a>ABOUT</a><a>SERVICES</a><a>TESTIMONIALS</a><a>GALLERY</a><a>CONTACT</a>
  </nav>
</header>

<section class="hero" role="img" aria-label="Photo of a two-storey painted family home with garden">
  <svg class="hero-curve" width="1200" height="600"><path d="M1200 440 Q1200 600 1040 600 L1200 600Z" fill="#f1f2f4"/></svg>
  <div class="hero-text">
    <h1>WELCOME TO FENWICK PAINTERS</h1>
    <p>Fenwick Painters Here at Fenwick Painters, we take a<br>lot of pride in our work.</p>
    <span class="btn-light">GET STARTED</span>
  </div>
  <div class="arrow-btn" style="left:40px;top:281px"><svg width="12" height="14"><path d="M9 1L3 7l6 6" stroke="#141a24" stroke-width="2.5" fill="none"/></svg></div>
  <div class="arrow-btn" style="left:1122px;top:281px"><svg width="12" height="14"><path d="M3 1l6 6-6 6" stroke="#141a24" stroke-width="2.5" fill="none"/></svg></div>
</section>
<div class="hero-dot"><i></i></div>

<section class="about">
  <div class="about-photo" role="img" aria-label="Circular photo of a painted house framed by an archer illustration"></div>
  <div class="about-text">
    <h2>ABOUT <span>US</span></h2>
    <p>Here at Fenwick Painters, we take a lot of pride in our work. We strive to ensure the highest quality paint-work, paying close attention to detail to provide a long lasting finish.</p>
    <p>Our clients are always our priority, we aim to deliver beyond their expectations. It is our goal to provide an excellent service from start to finish through clear communication, free quoting and transparency with our pricing.</p>
    <span class="btn-brown">LEARN MORE</span>
  </div>
</section>

<section class="services">
  <h2 class="section-title" style="top:76px"><span class="accent">OUR</span> SERVICES</h2>
  <div class="outline-arrow" style="left:40px;top:273px"><svg width="12" height="14"><path d="M9 1L3 7l6 6" stroke="#141a24" stroke-width="2.5" fill="none"/></svg></div>
  <div class="outline-arrow" style="left:1122px;top:273px"><svg width="12" height="14"><path d="M3 1l6 6-6 6" stroke="#141a24" stroke-width="2.5" fill="none"/></svg></div>

  <div class="service" style="left:111px">
    <div class="service-photo" role="img" aria-label="Photo of a freshly painted house exterior"></div>
    <div class="service-icon"><svg width="44" height="40" viewBox="0 0 44 40" fill="none" stroke="#fff" stroke-width="2"><path d="M4 18L22 4l18 14M8 15v22h28V15M14 24h6v13M26 24h6v6h-6z"/></svg></div>
    <h3>EXTERIOR PAINTING</h3>
  </div>
  <div class="service" style="left:360px">
    <div class="service-photo" style="background:linear-gradient(180deg,#d8d6d0,#9a9590 60%,#5c5550)" role="img" aria-label="Photo of a painted kitchen interior"></div>
    <div class="service-icon"><svg width="30" height="40" viewBox="0 0 30 40" fill="none" stroke="#fff" stroke-width="2"><rect x="3" y="3" width="24" height="10" rx="2"/><path d="M15 13v6H8v6M8 25v12"/></svg></div>
    <h3>INTERIOR PAINTING</h3>
  </div>
  <div class="service" style="left:609px">
    <div class="service-photo" style="background:linear-gradient(135deg,#c9cbc4,#6f7a68 50%,#4a5446)" role="img" aria-label="Photo of a patterned wallpaper wall"></div>
    <div class="service-icon"><svg width="38" height="38" viewBox="0 0 38 38" fill="none" stroke="#fff" stroke-width="2"><rect x="3" y="3" width="32" height="32"/><path d="M14 3v32M24 3v32"/></svg></div>
    <h3>WALLPAPERING</h3>
  </div>
  <div class="service" style="left:857px">
    <div class="service-photo" style="background:linear-gradient(180deg,#8fb0d4,#8e8070 55%,#4f7a38)" role="img" aria-label="Photo of a house after waterblasting"></div>
    <div class="service-icon"><svg width="40" height="40" viewBox="0 0 40 40" fill="none" stroke="#fff" stroke-width="2"><path d="M4 18L20 5l16 13M8 15v21h24V15M16 36v-9h8v9"/></svg></div>
    <h3>WATERBLASTING &amp;<br>HOUSE CLEANING</h3>
  </div>
</section>

<section class="testimonials" role="region" aria-label="Testimonials over a faded house photo">
  <h2 class="section-title">TESTIMONIALS</h2>
  <div class="t-card" style="left:111px">
    <div class="avatar" role="img" aria-label="Client portrait"></div>
    <span class="quote-mark" style="left:18px;top:100px">&ldquo;</span><span class="quote-mark" style="right:18px;top:160px">&rdquo;</span>
    <p>Very happy with Fenwick decorators. Tomas and Rowan did a great job with good communication and attention to detail. Definitely recommend... good value for money!</p>
    <div class="name">-HAROLD QUINCE</div>
  </div>
  <div class="t-card" style="left:446px">
    <div class="avatar" role="img" aria-label="Client portrait"></div>
    <span class="quote-mark" style="left:18px;top:100px">&ldquo;</span><span class="quote-mark" style="right:18px;top:160px">&rdquo;</span>
    <p>Tomas and Rowan was prompt and efficient. Very friendly and knowledgeable. Everything was done better than I expected. I would highly recommend them for anyone looking for painters.</p>
    <div class="name">-MILO SERRAT</div>
  </div>
  <div class="t-card" style="left:780px">
    <div class="avatar" role="img" aria-label="Client portrait"></div>
    <span class="quote-mark" style="left:18px;top:100px">&ldquo;</span><span class="quote-mark" style="right:18px;top:160px">&rdquo;</span>
    <p>We could not be happier with the work done painting the exterior of our two storey home. Tomas and Rowan had brilliant communication and the job went very smoothly. Would definitely recommend!</p>
    <div class="name">-LEONA BIRCH</div>
  </div>
</section>
<div class="dots"><i></i><i class="on"></i><i></i><i></i></div>

<section class="gallery">
  <h2 class="section-title" style="top:86px"><span class="accent">OUR</span> GALLERY</h2>
  <div class="g-photo" style="left:111px;background:linear-gradient(180deg,#c8ccd0,#8f9aa3 55%,#5b7a3e)" role="img" aria-label="Photo of a painted weatherboard villa"></div>
  <div class="g-photo" style="left:356px;background:linear-gradient(180deg,#e6e3dc,#a9a59c 55%,#2d3a55)" role="img" aria-label="Photo of a painted living room"></div>
  <div class="g-photo" style="left:600px;background:linear-gradient(180deg,#3d78c4,#9aa3ad 55%,#6b4b32)" role="img" aria-label="Photo of a painted house with deck"></div>
  <div class="g-photo" style="left:844px;background:linear-gradient(180deg,#d3dbe0,#7a8088 55%,#3f4a36)" role="img" aria-label="Photo of a grey painted house"></div>
  <div class="g-photo" style="left:1089px;background:linear-gradient(180deg,#e8e6e2,#b9b3ac 60%,#2b2b2b)" role="img" aria-label="Photo of a painted kitchen"></div>
</section>

<section class="contact">
  <h2 class="section-title" style="top:56px;font-size:28px"><span class="accent">CONTACT</span> INFORMATION</h2>
  <div class="c-item" style="left:158px">
    <div class="c-icon"><svg width="28" height="34" viewBox="0 0 28 34"><path fill="#7a5a36" d="M14 2a9 9 0 019 9c0 7-9 15-9 15S5 18 5 11a9 9 0 019-9zm0 5a4 4 0 100 8 4 4 0 000-8zM2 30h24v2H2z"/></svg></div>
    <div><h4>ADDRESS:</h4><p>Rowan Ashcombe<br>Kestrel Bay, Waikato.</p></div>
  </div>
  <div class="c-item" style="left:479px">
    <div class="c-icon"><svg width="34" height="34" viewBox="0 0 24 24"><path fill="#7a5a36" d="M6.6 10.8a15 15 0 006.6 6.6l2.2-2.2c.3-.3.7-.4 1-.2 1.1.4 2.3.6 3.6.6.6 0 1 .4 1 1V20c0 .6-.4 1-1 1A17 17 0 013 4c0-.6.4-1 1-1h3.5c.6 0 1 .4 1 1 0 1.3.2 2.5.6 3.6.1.3 0 .7-.2 1z"/></svg></div>
    <div><h4>PHONE:</h4><p>021 555 0148</p></div>
  </div>
  <div class="c-item" style="left:760px">
    <div class="c-icon"><svg width="36" height="26" viewBox="0 0 24 18"><path fill="#7a5a36" d="M0 0h24v2L12 9 0 2zM0 4l12 7 12-7v14H0z"/></svg></div>
    <div><h4>EMAIL:</h4><p>hello@fenwickpainters.co.nz</p></div>
  </div>
</section>

<footer class="footer">
  <svg class="footer-bg" width="1200" height="397"><path d="M0 160 Q0 0 160 0 L1200 0 L1200 397 L0 397Z" fill="#141a24"/></svg>
  <div class="footer-logo">FENWICK<br><span style="font-size:12px;letter-spacing:2px">PAINTERS</span></div>
  <div class="f-col" style="left:367px">
    <h5>QUICK LINKS</h5>
    <ul><li><b></b>Home</li><li><b></b>About</li><li><b></b>Services</li><li><b></b>Testimonials</li><li><b></b>Gallery</li><li><b></b>Contact</li></ul>
  </div>
  <div class="f-col" style="left:623px">
    <h5>OTHER LINKS</h5>
    <ul><li><b></b>Privacy Policy</li><li><b></b>Terms Of Use</li><li><b></b>Legal Support</li><li><b></b>Site Map</li></ul>
  </div>
  <div class="f-col" style="left:880px">
    <h5>CONTACT INFO</h5>
    <ul><li class="gap"><b></b>Rowan Ashcombe<br>Kestrel Bay, Waikato.</li><li class="gap"><b></b>021 555 0148</li><li><b></b>hello@fenwickpainters.co.nz</li></ul>
  </div>
  <div class="f-rule" style="top:271px"></div>
  <div class="badge" style="left:339px;width:134px" role="img" aria-label="Paint supplier badge"></div>
  <div class="badge" style="left:478px;width:326px" role="img" aria-label="Accredited painter badge"></div>
  <div class="f-rule" style="top:350px"></div>
  <div class="copyright">© 2022 FENWICK PAINTER &nbsp;|&nbsp; All Rights Reserved</div>
</footer>

</body>
</html>
```